VOMRA Pty Ltd Business Card

Looking for a simple yet eye-catching double-sided business card design using my company logo on one side and contact details on the other.

Target Market(s)

Government

Industry/Entity Type

Communication Systems Engineering

Contact Information for Business Card

VOMRA Pty Ltd

Requirements
Nice to have
• Would be great to have a QR code so details can be scanned into contacts

```html
<!DOCTYPE html>
<html lang="en">
<head>
<meta charset="utf-8">
<title>VOMRA Pty Ltd Business Card</title>
<link rel="stylesheet" href="https://fonts.googleapis.com/css2?family=Montserrat:wght@400;700&display=swap">
<style>
  :root {
    --bg: #e4e4e2;
    --card: #ffffff;
    --slate: #37434a;
    --ink: #1f2326;
    --black: #050505;
    --rule: #3c464c;
  }
  * { margin: 0; padding: 0; box-sizing: border-box; }
  html, body { width: 1200px; height: 801px; overflow: hidden; }
  body {
    background: var(--bg);
    font-family: "Montserrat", sans-serif;
    color: var(--ink);
    position: relative;
  }
  .card {
    position: absolute;
    top: 245px;
    width: 540px;
    height: 310px;
    background: var(--card);
    border-radius: 18px;
    overflow: hidden;
    box-shadow: 0 10px 30px rgba(0,0,0,0.12);
  }
  .card--front { left: 40px; }
  .card--back { left: 620px; }

  .edge-band {
    position: absolute;
    top: 0; right: 0;
    width: 60px; height: 100%;
  }

  .brand {
    position: absolute;
    font-weight: 700;
    color: var(--slate);
    letter-spacing: 0.04em;
  }
  .card--front .brand {
    left: 40px; top: 50%;
    transform: translateY(-50%);
    font-size: 44px;
  }
  .card--back .brand {
    left: 50%; top: 50%;
    transform: translate(-50%, -50%);
    font-size: 82px;
  }

  .divider {
    position: absolute;
    left: 250px; top: 40px;
    width: 1.5px; height: 230px;
    background: var(--rule);
  }

  .details {
    position: absolute;
    left: 272px; top: 42px;
    width: 215px;
  }
  .person-name {
    font-weight: 700;
    font-size: 20px;
    color: var(--slate);
    letter-spacing: 0.02em;
  }
  .person-role {
    font-size: 13px;
    margin-top: 2px;
  }
  .contact-list {
    list-style: none;
    margin-top: 22px;
    font-size: 12.5px;
  }
  .contact-list li {
    display: flex;
    align-items: center;
    gap: 8px;
    line-height: 22px;
  }
  .contact-list svg { width: 12px; height: 12px; flex: none; fill: var(--ink); }
  .address {
    margin-top: 18px;
    font-size: 12.5px;
    line-height: 18px;
  }
</style>
</head>
<body>
  <section class="card card--front" aria-label="Card front with contact details">
    <div class="brand">VOMRA</div>
    <div class="divider"></div>
    <div class="details">
      <p class="person-name">DANIEL HARTLEY</p>
      <p class="person-role">Managing Director</p>
      <ul class="contact-list">
        <li>
          <svg viewBox="0 0 12 12" aria-hidden="true"><path d="M3 1l2 2.5-1.2 1.3a6 6 0 0 0 3.4 3.4L8.5 7 11 9l-1.3 2C5.5 11 1 6.5 1 2.3z"/></svg>
          987 654 321
        </li>
        <li>
          <svg viewBox="0 0 12 12" aria-hidden="true"><path d="M1 3h10v6.5H1z M1 3l5 3.5L11 3" stroke="#fff" stroke-width="0.8"/></svg>
          admin@vomra.com.au
        </li>
        <li>
          <svg viewBox="0 0 12 12" aria-hidden="true"><circle cx="6" cy="6" r="5"/><path d="M1 6h10M6 1v10" stroke="#fff" stroke-width="0.8"/></svg>
          www.vomra.com.au
        </li>
      </ul>
      <p class="address">42-46 Marlow Street Redfern<br>NSW 2016 Australia</p>
    </div>
    <svg class="edge-band" viewBox="0 0 60 310" preserveAspectRatio="none" aria-hidden="true">
      <polygon points="32,0 60,0 60,310 32,310" fill="var(--black)"/>
      <polygon points="0,310 60,310 60,190 22,190 0,230" fill="var(--slate)"/>
    </svg>
  </section>

  <section class="card card--back" aria-label="Card back with company name">
    <div class="brand">VOMRA</div>
  </section>
</body>
</html>
```